VENTURE CAPITAL GROUP BUSINESS CARD DESIGN

Venture Capital Group based in SF looking for a bold business card design. No trendy colour explosion, 3D effects etc. Just "simple" optical effects. Works on your brain, keeps your eye focused and sticks to your mind.
Target Market(s)
Technology startups
Industry/Entity Type
Venture Capital
Contact Information for Business Card
DESMOND WHITLAKE
MANAGING PARTNER
187 FENWORTH ST SAN FRANCISCO, CA 94187
415.555.0142 O
415.555.0147 F
415.555.0193 C
desmond@veldtmoorcapital.ventures

```html
<!DOCTYPE html>
<html lang="en">
<head>
<meta charset="utf-8">
<title>Veldtmoor Capital Group – Business Card</title>
<link rel="stylesheet" href="https://fonts.googleapis.com/css2?family=Cinzel:wght@500&family=Lora:wght@400;600&display=swap">
<style>
  :root {
    --backdrop: #a9a6a7;
    --card: #fbfbfb;
    --card-edge: #e4e4e4;
    --green-light: #4fb94a;
    --green-dark: #137336;
    --green-text: #1e8a3c;
    --ink: #555657;
    --ink-soft: #6a6b6c;
    --rule-gray: #b9b9b9;
    --disc: #ececec;
  }
  * { box-sizing: border-box; margin: 0; padding: 0; }
  html, body {
    width: 1200px; height: 1200px; overflow: hidden;
    background: var(--backdrop);
  }
  .canvas { position: relative; width: 1200px; height: 1200px; }

  .card {
    position: absolute;
    width: 713px; height: 418px;
    background: var(--card);
    border: 1px solid var(--card-edge);
  }
  .card--front { left: 238px; top: 118px; }
  .card--back  { left: 229px; top: 644px; overflow: hidden; }

  .brand-disc {
    position: absolute; border-radius: 50%;
    background: radial-gradient(circle at 40% 35%, #ffffff 0%, var(--disc) 75%, #dedede 100%);
  }
  .card--front .brand-disc { left: 280px; top: 96px; width: 142px; height: 142px; }
  .brand-name {
    position: absolute;
    font-family: "Cinzel", serif; font-weight: 500;
    color: var(--green-text);
    white-space: nowrap; letter-spacing: 0.06em;
  }
  .card--front .brand-name {
    left: 0; right: 0; top: 300px; text-align: center; font-size: 32px;
  }

  .side-band {
    position: absolute; left: 0; top: 0; bottom: 0; width: 60px;
    background: linear-gradient(180deg, var(--green-light) 0%, var(--green-dark) 100%);
  }
  .side-rule {
    position: absolute; left: 60px; top: 0; bottom: 0; width: 7px;
    background: var(--rule-gray);
  }
  .card--back .brand-disc { left: 100px; top: 50px; width: 90px; height: 90px; }
  .card--back .brand-name { left: 212px; top: 78px; font-size: 27px; }

  .person { position: absolute; left: 93px; top: 208px; font-family: "Lora", serif; }
  .person__name { font-size: 25px; font-weight: 600; color: var(--ink); }
  .person__title { font-size: 16px; color: var(--ink-soft); margin-top: 4px; }

  .contacts {
    position: absolute; top: 302px;
    list-style: none; font-family: "Lora", serif; font-size: 17.5px; color: var(--ink-soft);
  }
  .contacts--phones { left: 93px; }
  .contacts--online { left: 306px; }
  .contacts li { display: flex; align-items: center; height: 26px; white-space: nowrap; }
  .contacts svg { width: 18px; height: 18px; margin-right: 18px; fill: var(--green-dark); flex: none; }
</style>
</head>
<body>
<main class="canvas">

  <section class="card card--front" aria-label="Card front">
    <div class="brand-disc"></div>
    <div class="brand-name">Veldtmoor Capital Group</div>
  </section>

  <section class="card card--back" aria-label="Card back">
    <div class="side-band"></div>
    <div class="side-rule"></div>
    <div class="brand-disc"></div>
    <div class="brand-name">Veldtmoor Capital Group</div>

    <div class="person">
      <div class="person__name">Desmond Whitlake</div>
      <div class="person__title">Managing Partner</div>
    </div>

    <ul class="contacts contacts--phones">
      <li><svg viewBox="0 0 20 20" aria-hidden="true"><path d="M2 7c0-2 3-4 8-4s8 2 8 4v2h-4V7H6v2H2z"/><path d="M5 10h10l2 7H3z"/></svg>415.555.0142</li>
      <li><svg viewBox="0 0 20 20" aria-hidden="true"><rect x="5" y="2" width="10" height="5"/><rect x="2" y="8" width="16" height="7" rx="1"/><rect x="5" y="13" width="10" height="5" fill="#fff" stroke="#137336" stroke-width="1.5"/></svg>415.555.0147</li>
      <li><svg viewBox="0 0 20 20" aria-hidden="true"><rect x="5" y="1" width="10" height="18" rx="2"/><rect x="7" y="4" width="6" height="10" fill="#fff"/></svg>415.555.0193</li>
    </ul>

    <ul class="contacts contacts--online">
      <li><svg viewBox="0 0 20 20" aria-hidden="true"><rect x="1" y="4" width="18" height="12"/><path d="M1 4l9 7 9-7" fill="none" stroke="#fff" stroke-width="1.6"/></svg>desmond@veldtmoorcapital.ventures</li>
      <li><svg viewBox="0 0 20 20" aria-hidden="true"><circle cx="10" cy="10" r="8"/><path d="M2 10h16M10 2v16M4 6h12M4 14h12" stroke="#fff" stroke-width="1.1" fill="none"/><ellipse cx="10" cy="10" rx="3.5" ry="8" fill="none" stroke="#fff" stroke-width="1.1"/></svg>www.veldtmoorcapital.ventures</li>
      <li><svg viewBox="0 0 20 20" aria-hidden="true"><path d="M10 1a6 6 0 0 1 6 6c0 5-6 12-6 12S4 12 4 7a6 6 0 0 1 6-6z"/><circle cx="10" cy="7" r="2.3" fill="#fff"/></svg>187 Fenworth St San Francisco, CA 94187</li>
    </ul>
  </section>

</main>
</body>
</html>
```